English and Spanish Language School Needs a Business Card

Need a business card design a startup company called Maribel Language School. The company will offer English and Spanish conversational level courses designed to make the learner feel comfortable with grammar and vocabulary. We would like to see a logo with some colour that should communicate learning, growth.

Target Market(s)

Consumers and businesses

Industry/Entity Type

Education

Contact Information for Business Card

TBD

Font styles to use
Serif

Requirements
Must have
• Include the following
• Logo
• Name
• Title
• Cellphone Number
• Office Phone number
• Email address
• Office Address

```html
<!DOCTYPE html>
<html lang="en">
<head>
<meta charset="utf-8">
<title>Maribel Language School – Business Card</title>
<link rel="stylesheet" href="https://fonts.googleapis.com/css2?family=Montserrat:wght@400;500;700&display=swap">
<style>
  :root {
    --stage: #e9e6e1;
    --card-light: #2f4545;
    --card-dark: #0b1212;
    --brand-red: #d3232f;
    --brand-teal: #1597a3;
    --ink-white: #ffffff;
    --ink-soft: #e6ecec;
  }
  * { box-sizing: border-box; margin: 0; padding: 0; }
  html, body {
    width: 1200px; height: 913px; overflow: hidden;
    background: var(--stage);
    font-family: "Montserrat", sans-serif;
  }
  .canvas {
    position: relative; width: 1200px; height: 913px;
  }
  .card {
    position: absolute; width: 560px; height: 320px;
    border-radius: 14px; overflow: hidden;
    background: linear-gradient(155deg, var(--card-light) 0%, #152020 55%, var(--card-dark) 100%);
    box-shadow: 0 12px 30px rgba(0,0,0,.25);
  }
  .card--front { left: 30px; top: 150px; }
  .card--back  { left: 610px; top: 443px; }

  .teal-edge {
    position: absolute; left: 0; right: 0; bottom: 0; height: 12px;
    background: var(--brand-teal);
  }

  /* front */
  .front-brand {
    position: absolute; left: 34px; top: 62px; width: 230px;
    font-size: 24px; font-weight: 700; line-height: 1.15;
    color: var(--brand-red);
  }
  .holder {
    position: absolute; right: 36px; top: 66px; text-align: right;
    color: var(--brand-red);
  }
  .holder__name { font-size: 22px; font-weight: 700; letter-spacing: .5px; }
  .holder__title { font-size: 12px; font-weight: 500; margin-top: 2px; }
  .divider {
    position: absolute; left: 30px; right: 30px; top: 150px;
    height: 2px; background: var(--ink-white);
  }
  .contacts {
    position: absolute; left: 34px; top: 180px; list-style: none;
  }
  .contacts li {
    display: flex; align-items: center; gap: 10px;
    font-size: 13px; color: var(--ink-soft); line-height: 24px;
  }
  .contacts li.contacts__web { font-weight: 700; color: var(--ink-white); }
  .contacts svg { width: 12px; height: 12px; flex: none; }
  .address-tab {
    position: absolute; right: 0; bottom: 0; width: 200px; height: 100px;
    background: var(--brand-red); border-top-left-radius: 46px;
    padding: 22px 26px 0 0; text-align: right;
    color: var(--ink-white); font-size: 15px; line-height: 22px;
  }

  /* back */
  .back-brand {
    position: absolute; left: 0; right: 0; top: 92px; text-align: center;
    font-size: 46px; font-weight: 700; line-height: 1.05;
    color: var(--ink-white);
  }
  .web-tab {
    position: absolute; left: 0; bottom: 0; width: 300px; height: 72px;
    background: var(--brand-red); border-top-right-radius: 56px;
    padding: 34px 0 0 26px;
    color: var(--ink-white); font-size: 14px; font-weight: 700; letter-spacing: .3px;
  }
</style>
</head>
<body>
<main class="canvas">

  <section class="card card--front" aria-label="Business card front">
    <div class="teal-edge"></div>
    <p class="front-brand">Maribel Language School</p>
    <div class="holder">
      <p class="holder__name">Lena Whitford</p>
      <p class="holder__title">Director</p>
    </div>
    <div class="divider"></div>
    <ul class="contacts">
      <li>
        <svg viewBox="0 0 12 12"><rect x="1" y="2" width="10" height="8" rx="1" fill="none" stroke="var(--brand-red)" stroke-width="1.4"/></svg>
        +330 2471-8830
      </li>
      <li>
        <svg viewBox="0 0 12 12"><path d="M3 1 L5 3.5 L4 5 Q5.5 7.5 7 8 L8.5 7 L11 9 L9.5 11 Q4 10 1 2.5 Z" fill="var(--brand-red)"/></svg>
        +330 2459-1627
      </li>
      <li>
        <svg viewBox="0 0 12 12"><rect x="1" y="2.5" width="10" height="7" fill="none" stroke="var(--brand-red)" stroke-width="1.3"/><path d="M1 2.5 L6 7 L11 2.5" fill="none" stroke="var(--brand-red)" stroke-width="1.3"/></svg>
        hello@maribelschool.com
      </li>
      <li class="contacts__web">
        <svg viewBox="0 0 12 12"><circle cx="6" cy="6" r="4.8" fill="none" stroke="var(--brand-red)" stroke-width="1.3"/><path d="M1.2 6 H10.8 M6 1.2 V10.8" stroke="var(--brand-red)" stroke-width="1"/></svg>
        maribelschool.com
      </li>
    </ul>
    <div class="address-tab">
      <p>Po Box 218</p>
      <p>Glenview VIC 3920</p>
    </div>
  </section>

  <section class="card card--back" aria-label="Business card back">
    <div class="teal-edge" style="height:30px"></div>
    <p class="back-brand">Maribel<br>Language School</p>
    <p class="web-tab">www.maribelschool.com</p>
  </section>

</main>
</body>
</html>
```